Bluefern Business Services needs a new interactive and interesting website

We need an interesting, professional, modern and functional company website for Bluefern Business Services - a young IT Services company based out of Chennai, India.

Bluefern Business Services is a fully owned subsidiary of Marlow Goods, one of the world's leading direct to consumer wine merchant.

We already have a registered company logo which must feature in the website.

We conceive, design, develop, test, implement and support IT solutions across the entire Marlow Goods IT landscape. For ex : We currently run about 25 e-commerce websites for Marlow Goods on ATG and Dot Net.

We would like to see our corporate colors used in the website. (Burgundy wine and wine green - source: www.bluefernbs-site.com)

We are looking at this website to communicate a fun, friendly and professionally managed company - reaching out to career seekers, prospective customers and general public.

For reference - The company name 'Bluefern' is an inspiration from the Marlow Goods lineage.

The second image with the world map is stickered on our main entrance to the office, I am not sure where this can be used -just putting it out there..

Please note that there are only a few more days to submit designs for this contest  !

I would appreciate if you can help posting your designs in time for our review and consideration.

Thanks.

Reason: Thanks for your inputs. We have a number of designers and a lot to digest and work with in the past few days. There has been a rush of new designs in the last few days Hence we will require more time to process these and make our decision. Hence i am requesting the contest to be open for more days. Regards, Tarun

Target Market(s)

Prospective job seekers who want to know more about the company and also wish to apply for a job vacancy
People wanting to know more about the company in general and our progress
People who want to see what we offer and how we can help them too - prospective customers
Companies that are interested in our IT Captive journey and are looking for a business opportunity

Industry/Entity Type

E-Commerce

Requirements
Must have
• Log In/ Register facility acting as a Single Sign on for Intranet (Employees)

Facility to post job vacancies (with an expiry date) and enable people to apply for a role and upload their CV/Resume.

Facility to Review Job applications

Facility for website visitors to contact Bluefern business Services via an online 'Contact Us' form with a split of job seekers and business opportunities

Gallery facility to upload pictures regarding company events
Nice to have
• Less Cluttered and contemporary design
Some Wine/Vineyard inspirations will be good but not too much, the company is an IT services company

```html
<!DOCTYPE html>
<html lang="en">
<head>
<meta charset="utf-8">
<title>Bluefern Business Services</title>
<link href="https://fonts.googleapis.com/css2?family=Open+Sans:wght@400;600;700&display=swap" rel="stylesheet">
<style>
  :root{
    --burgundy:#8a0040;
    --olive:#4a4a10;
    --olive-btn:#4b4b0e;
    --panel:#f1f1f1;
    --line:#d8d8d8;
    --text:#333;
    --muted:#888;
    --blue:#3a7fc0;
    --dark:#222;
  }
  *{box-sizing:border-box;margin:0;padding:0}
  html,body{width:1200px;height:1191px;overflow:hidden;background:#fff;font-family:"Open Sans",Arial,sans-serif;color:var(--text)}
  .page{position:relative;width:1200px;height:1191px}
  .abs{position:absolute}

  .masthead{left:0;top:0;width:1200px;height:163px;background:var(--burgundy);border-bottom:2px solid #6d0033}
  .brand{left:118px;top:34px;display:flex;align-items:center;gap:10px;color:#fff;font-weight:600}
  .brand-mark{width:36px;height:36px;border-radius:50%;background:#fff}
  .brand-name{font-size:40px;line-height:40px;letter-spacing:-.5px}
  .brand-sub{font-size:27px;line-height:32px}
  .social{top:52px;left:888px;display:flex;gap:10px}
  .social span{width:32px;height:32px;display:block}

  .navbar{left:110px;top:140px;width:980px;height:47px;background:linear-gradient(#fafafa,#e6e6e6);border:1px solid #cfcfcf;display:flex;align-items:center}
  .nav-item{font-size:14px;color:#444;padding:0 20px;height:27px;line-height:27px;border-right:1px solid #d4d4d4}
  .nav-item:last-child{border-right:none}
  .nav-item.active{color:var(--burgundy);text-transform:uppercase;padding-left:21px;padding-right:19px}
  .search{left:811px;top:148px;width:272px;height:34px;background:#fff;border:1px solid #ccc;border-radius:2px;font-size:12px;color:#999;padding:9px 8px}

  .content{left:110px;top:197px;width:980px;height:931px;background:var(--panel)}
  .hero{left:118px;top:204px;width:964px;height:365px;background:linear-gradient(90deg,#f6f6f5 0%,#eceeef 38%,#c5ccd3 62%,#9aa6b2 82%,#d8dde2 100%)}
  .hero-title{left:137px;top:298px;font-size:29px;color:var(--olive);letter-spacing:-.5px}
  .hero-title b{font-weight:600}
  .hero-copy{left:139px;top:351px;width:340px;font-size:13px;line-height:20px;color:#333}
  .btn-read{left:138px;top:473px;width:106px;height:41px;background:var(--olive-btn);color:#fff;font-size:14px;line-height:41px;text-align:center;border-bottom:2px solid #2f2f06}

  .register{left:118px;top:587px;width:964px;height:70px;background:#ececec;border:1px solid var(--line)}
  .field{top:606px;width:245px;height:31px;background:#fff;border:1px solid #ccc;font-size:12px;color:#aaa;padding:7px 10px}
  .btn-register{left:934px;top:606px;width:136px;height:31px;background:var(--dark);color:#fff;font-size:16px;line-height:31px;text-align:center;border-radius:2px}

  .service{top:686px;width:215px}
  .service h3{font-size:14px;font-weight:400;color:#333;display:flex;align-items:center;gap:6px;height:22px}
  .service p{margin-top:9px;font-size:12px;line-height:20px;color:var(--muted)}

  .section-title{font-size:19px;font-weight:400}
  .gallery-title{left:129px;top:880px;color:var(--burgundy)}
  .gallery-rule{left:129px;top:909px;width:689px;height:1px;background:var(--line)}
  .gallery-rule::before{content:"";position:absolute;left:0;top:-1px;width:109px;height:3px;background:var(--burgundy)}
  .testi-title{left:838px;top:876px;color:#444;font-size:20px}
  .testi-rule{left:838px;top:909px;width:220px;height:1px;background:var(--line)}
  .testi-rule::before{content:"";position:absolute;left:0;top:-1px;width:100px;height:3px;background:var(--blue)}
  .arrows{display:flex;gap:2px}
  .arrows span{width:23px;height:22px;background:#a9a9a9;color:#fff;font-size:13px;text-align:center;line-height:21px}

  .thumb{top:931px;width:211px;height:118px}
  .btn-upload{left:138px;top:1067px;width:134px;height:33px;background:#b8b8b8;color:#222;font-size:14px;line-height:33px;text-align:center;border-radius:2px}

  .quote{left:838px;top:931px;width:220px;height:135px;background:#e2e2e2;padding:20px 20px;font-size:12px;line-height:24px;color:#666}
  .quote a{color:#333;text-decoration:none}
  .author{left:887px;top:1079px;font-size:13px;font-weight:600;color:#222}
  .author small{font-size:10px;font-weight:400;color:#888}
  .author small em{font-style:normal;color:var(--blue)}

  .copyright{left:0;top:1151px;width:1200px;text-align:center;font-size:13px;color:#333}
</style>
</head>
<body>
<div class="page">

  <header class="masthead abs"></header>
  <div class="brand abs">
    <span class="brand-mark"></span>
    <div>
      <div class="brand-name">Bluefern</div>
      <div class="brand-sub">Business Services</div>
    </div>
  </div>
  <div class="social abs" aria-label="Social links">
    <span style="background:#3b5998"></span>
    <span style="background:#1da1f2"></span>
    <span style="background:#0e76a8"></span>
    <span style="background:#dd4b39"></span>
    <span style="background:#00aff0"></span>
  </div>

  <nav class="navbar abs">
    <span class="nav-item active">Home</span>
    <span class="nav-item">About Us</span>
    <span class="nav-item">Clients</span>
    <span class="nav-item">Services</span>
    <span class="nav-item">Careers</span>
    <span class="nav-item">Contact Us</span>
  </nav>
  <div class="search abs">Search
    <svg style="position:absolute;right:9px;top:7px" width="20" height="20" viewBox="0 0 20 20"><circle cx="8" cy="8" r="6.5" fill="none" stroke="#8a0040" stroke-width="2.6"/><line x1="13" y1="13" x2="18.5" y2="18.5" stroke="#8a0040" stroke-width="3" stroke-linecap="round"/></svg>
  </div>

  <main class="content abs"></main>

  <div class="hero abs" role="img" aria-label="Photo of a team of office colleagues working together at laptops"></div>
  <h1 class="hero-title abs" style="font-weight:400">Delivering <b>IT Excellence</b></h1>
  <p class="hero-copy abs">Welcome to Bluefern Business Services, an emerging provider of global IT consulting and software services. We are part of the Marlow Goods group, a family run business and the world's largest multi-channel home delivery wine merchant.</p>
  <div class="btn-read abs">Read More</div>

  <section class="register abs"></section>
  <svg class="abs" style="left:138px;top:610px" width="36" height="24" viewBox="0 0 36 24">
    <g fill="#111"><rect x="0" y="0" width="5" height="4"/><rect x="8" y="0" width="28" height="4"/><rect x="0" y="7" width="5" height="4"/><rect x="8" y="7" width="28" height="4"/><rect x="0" y="14" width="5" height="4"/><rect x="8" y="14" width="28" height="4"/><rect x="0" y="20" width="5" height="4"/><rect x="8" y="20" width="28" height="4"/></g>
  </svg>
  <div class="field abs" style="left:183px">First Name</div>
  <div class="field abs" style="left:433px">Last Name</div>
  <div class="field abs" style="left:683px">Email</div>
  <div class="btn-register abs">REGISTER</div>

  <div class="service abs" style="left:138px">
    <h3><svg width="18" height="18" viewBox="0 0 18 18"><rect width="18" height="18" fill="#333"/><rect x="7.5" y="3" width="3" height="3" fill="#fff"/><rect x="7.5" y="7.5" width="3" height="8" fill="#fff"/></svg>Packaged Applications</h3>
    <p>Lorem ipsum dolor sit amet, consectetur adipiscing elit. Nulla tincidunt venenatis justo quis faucibus. Maecenas eget purus tellus, eget imperdiet ante.</p>
  </div>
  <div class="service abs" style="left:358px">
    <h3><svg width="18" height="14" viewBox="0 0 18 14"><rect width="18" height="14" fill="#333"/><g fill="#fff"><rect x="2" y="4" width="4" height="3"/><rect x="7" y="4" width="4" height="3"/><rect x="12" y="4" width="4" height="3"/><rect x="2" y="9" width="4" height="3"/><rect x="7" y="9" width="4" height="3"/><rect x="12" y="9" width="4" height="3"/></g></svg>Enterprise Application</h3>
    <p>Lorem ipsum dolor sit amet, consectetur adipiscing elit. Nulla tincidunt venenatis justo quis faucibus. Maecenas eget purus tellus, eget imperdiet ante.</p>
  </div>
  <div class="service abs" style="left:588px">
    <h3><svg width="19" height="16" viewBox="0 0 19 16"><path d="M0 5h4l6-5v16l-6-5H0z" fill="#333"/><path d="M13 4q3 4 0 8M15.5 1.5q5 6.5 0 13" stroke="#333" stroke-width="1.8" fill="none"/></svg>Digital Commerce</h3>
    <p>Lorem ipsum dolor sit amet, consectetur adipiscing elit. Nulla tincidunt venenatis justo quis faucibus. Maecenas eget purus tellus, eget imperdiet ante.</p>
  </div>
  <div class="service abs" style="left:818px">
    <h3><svg width="14" height="18" viewBox="0 0 14 18"><rect x="1" y="1" width="12" height="16" rx="1.5" fill="none" stroke="#333" stroke-width="2"/><rect x="5" y="13" width="4" height="2" fill="#333"/></svg>Development &amp; Maintenance</h3>
    <p>Lorem ipsum dolor sit amet, consectetur adipiscing elit. Nulla tincidunt venenatis justo quis faucibus. Maecenas eget purus tellus, eget imperdiet ante.</p>
  </div>

  <h2 class="section-title gallery-title abs">Our Gallery</h2>
  <div class="gallery-rule abs"></div>
  <div class="arrows abs" style="left:770px;top:877px"><span>&lsaquo;</span><span>&rsaquo;</span></div>

  <h2 class="section-title testi-title abs">Testimonials</h2>
  <div class="testi-rule abs"></div>
  <div class="arrows abs" style="left:1010px;top:877px"><span>&lsaquo;</span><span>&rsaquo;</span></div>

  <div class="thumb abs" style="left:138px;background:linear-gradient(160deg,#3b4a66,#6a7488 55%,#2c3346)" role="img" aria-label="Photo of a crowded job and internship fair hall"></div>
  <div class="thumb abs" style="left:367px;background:linear-gradient(135deg,#ffffff,#fbe9e5 60%,#f7d9a8)" role="img" aria-label="Poster for the national job fair in Northgate"></div>
  <div class="thumb abs" style="left:598px;background:linear-gradient(90deg,#e8e8e8 0%,#bdbdbd 35%,#111 60%,#000 100%)" role="img" aria-label="Poster of a businessman announcing the fall job fair"></div>
  <div class="btn-upload abs">UPLOAD PICTURE</div>

  <blockquote class="quote abs">It is a long established fact that a reader will be distracted by the readable content of a page...<a href="#">read more</a></blockquote>
  <svg class="abs" style="left:838px;top:1066px" width="60" height="26" viewBox="0 0 60 26"><path d="M33 0H58L33 24Z" fill="#e2e2e2"/><path d="M33 0V24L58 0" fill="none" stroke="#fff" stroke-width="1"/></svg>
  <svg class="abs" style="left:842px;top:1075px" width="16" height="20" viewBox="0 0 16 20"><circle cx="8" cy="5" r="4.5" fill="#666"/><path d="M0 20v-5q0-5 8-5t8 5v5z" fill="#666"/></svg>
  <div class="author abs">Daniel Reyes, <small>CEO, <em>Norvale Inc.</em></small></div>

  <footer class="copyright abs">Copyright Bluefern Business Services Private Limited.</footer>

</div>
</body>
</html>
```